Veltrano.co - Polar Expeditions Specialists

We need a modern, visually striking business card for Veltrano.co, a company specialized in selling expedition cruises to the most remote regions on Earth, with a focus on the Arctic and Antarctica. The design should instantly communicate that the cardholder is an expert in polar travel. Use clean, premium aesthetics with cool tones like icy blue and white, possibly incorporating polar imagery (ice, glaciers, penguins, etc.)

Attached the logo

Contact Information for Business Card

Feels high-end and trustworthy.. Visually memorable — encourages people to keep it

Colors
0054AA
0677BA
7BADD7
CADEEF
E8F1F8

Requirements
Must have
• ice, glaciers, penguins, montains
Nice to have
• modern, transparente,

```html
<!DOCTYPE html>
<html lang="en">
<head>
<meta charset="UTF-8">
<title>Veltrano.co – Business Card</title>
<link href="https://fonts.googleapis.com/css2?family=Poppins:wght@400;500;600;700&display=swap" rel="stylesheet">
<style>
  :root {
    --stage: #e6e8ec;
    --navy: #10112a;
    --white: #ffffff;
    --brand-blue: #2f6db5;
    --rule-blue: #2a64b0;
    --ink: #1a1c2a;
    --band-gray: #8a8d92;
    --ice-light: #cadeef;
  }
  * { margin: 0; padding: 0; box-sizing: border-box; }
  html, body {
    width: 1200px; height: 900px; overflow: hidden;
    background: var(--stage);
    font-family: "Poppins", sans-serif;
  }
  .card {
    position: absolute; left: 250px; width: 700px; height: 400px;
    border-radius: 26px; overflow: hidden;
    box-shadow: 0 6px 18px rgba(0,0,0,0.18);
  }
  .card--back { top: 40px; background: var(--navy); color: var(--white); }
  .card--front { top: 470px; background: var(--white); color: var(--ink); }

  .polar-mark { display: block; border-radius: 4px; }

  .back-brand {
    position: absolute; inset: 0;
    display: flex; flex-direction: column; align-items: center; justify-content: center;
    padding-top: 10px;
  }
  .back-brand .polar-mark {
    width: 110px; height: 110px; margin-bottom: 18px;
    background: var(--white);
  }
  .back-brand .wordmark { font-size: 70px; font-weight: 700; letter-spacing: 1px; line-height: 1; }
  .back-brand .tagline { font-size: 20px; font-weight: 500; margin-top: 10px; }

  .front-brand { position: absolute; left: 50px; top: 42px; display: flex; align-items: flex-end; gap: 24px; }
  .front-brand .polar-mark {
    width: 100px; height: 100px;
    background: var(--brand-blue);
  }
  .front-brand .text { color: var(--brand-blue); padding-bottom: 2px; }
  .front-brand .wordmark { font-size: 56px; font-weight: 700; line-height: 1; letter-spacing: 0.5px; }
  .front-brand .tagline { font-size: 16px; font-weight: 600; margin-top: 6px; }

  .holder { position: absolute; left: 60px; top: 186px; }
  .holder .name { font-size: 27px; font-weight: 700; color: var(--brand-blue); line-height: 1.1; }
  .holder .role { font-size: 16px; font-weight: 400; margin-top: 2px; }

  .rule { position: absolute; left: 60px; right: 60px; top: 258px; height: 2px; background: var(--rule-blue); }

  .contacts { position: absolute; left: 60px; top: 268px; list-style: none; font-size: 15px; line-height: 24px; }
  .contacts li { display: flex; align-items: center; gap: 10px; }
  .contacts svg { width: 13px; height: 13px; fill: var(--brand-blue); flex: none; }

  .address { position: absolute; right: 60px; top: 300px; font-size: 15px; line-height: 22px; }

  .band { position: absolute; left: 0; bottom: 0; width: 700px; height: 32px; }
</style>
</head>
<body>
  <section class="card card--back">
    <div class="back-brand">
      <span class="polar-mark" role="img" aria-label="Polar emblem: bear, penguins and ice"></span>
      <div class="wordmark">Veltrano.co</div>
      <div class="tagline">Polar Expeditions Specialists</div>
    </div>
  </section>

  <section class="card card--front">
    <div class="front-brand">
      <span class="polar-mark" role="img" aria-label="Polar emblem: bear, penguins and ice"></span>
      <div class="text">
        <div class="wordmark">Veltrano.co</div>
        <div class="tagline">Polar Expeditions Specialists</div>
      </div>
    </div>

    <div class="holder">
      <div class="name">Marlon Pike</div>
      <div class="role">CEO &amp; Founder</div>
    </div>

    <div class="rule"></div>

    <ul class="contacts">
      <li><svg viewBox="0 0 16 16" aria-hidden="true"><path d="M3 1l3 3-2 2c1 2 3 4 5 5l2-2 3 3-2 3C6 15 1 10 0 4z"/></svg>+1.555.014.278</li>
      <li><svg viewBox="0 0 16 16" aria-hidden="true"><path d="M0 3h16v10H0z M1 4l7 5 7-5" stroke="#fff" stroke-width="1"/></svg>hello@veltrano.co</li>
      <li><svg viewBox="0 0 16 16" aria-hidden="true"><circle cx="8" cy="8" r="8"/></svg>www.veltrano.co</li>
    </ul>

    <div class="address">48 Harbor Point Lane,<br>Lakewood, ME 04101 USA</div>

    <svg class="band" viewBox="0 0 700 32" preserveAspectRatio="none" aria-hidden="true">
      <polygon points="0,0 420,20 440,32 0,32" fill="var(--brand-blue)"/>
      <polygon points="420,20 700,32 440,32" fill="var(--band-gray)"/>
    </svg>
  </section>
</body>
</html>
```